lantern pathway for children needs a website designer

We need a website designer for our new extension to our company known as 'lantern pathway' providing shadow support services to children based in Singapore. We are a sister branch of a private clinic 'Bright horizons' providing speech language, occupational, and educational therapy to children.

We would like to use our own photos. So the selected design should have a frame with pictures to give us an idea but we will replace them with our own. We will be needing help with inputting information and changing information throughout.

We would like to see designs that are simple, and professional. We have a logo (see attached). The result should convey professionalism in shadow support, fostering independent thinking and moving students towards self-learning.

Target Market(s)

Teachers, psychologists, parents

Industry/Entity Type

Clinic

Requirements
Should not have
• too distracting colours

```html
<!DOCTYPE html>
<html lang="en">
<head>
<meta charset="utf-8">
<title>Lantern Pathway</title>
<link rel="stylesheet" href="https://fonts.googleapis.com/css2?family=Magra:wght@400;700&family=Noto+Sans:wght@400;700&display=swap">
<style>
:root{
  --nav-dark:#2e2b23;
  --nav-text:#efe8d6;
  --accent-red:#8c0d0d;
  --cream:#f5f2dc;
  --cream-light:#fcfae9;
  --band-brown:#7d6651;
  --title-red:#8f0b0b;
  --text-body:#4a4038;
  --news-band:#e6e3d4;
  --footer-dark:#2a2623;
  --footer-text:#9b938a;
  --footer-head:#87705a;
}
*{box-sizing:border-box;margin:0;padding:0}
html,body{width:1200px;height:1200px;overflow:hidden}
body{background:var(--cream);font-family:"Noto Sans",Verdana,sans-serif;color:var(--text-body);position:relative}
.container{position:absolute;left:157px;width:887px}

.top-strip{position:absolute;top:0;left:0;width:1200px;height:48px;background:linear-gradient(90deg,#3a2a14,#7a5526 12%,#3a2a14 14%,#7a5526 40%,#3a2a14 60%,#7a5526 86%,#3a2a14)}
.header-band{position:absolute;top:48px;left:0;width:1200px;height:158px;background:repeating-linear-gradient(135deg,var(--cream-light) 0 3px,#f7f3dc 3px 5px)}
.main-nav{top:0;height:83px;background:linear-gradient(#2a2720,#3b372d);border-bottom:5px solid var(--accent-red);display:flex;justify-content:space-around;align-items:center;padding:0 20px}
.main-nav a{font-family:"Magra",sans-serif;font-size:19px;color:var(--nav-text);text-decoration:none;position:relative;padding-top:14px}
.main-nav a.active::after{content:"";position:absolute;left:-11px;right:-11px;bottom:-27px;height:7px;background:#c9bfb5}

.brand{top:102px;font-family:"Magra",sans-serif;font-weight:700;font-size:44px;color:var(--accent-red);display:flex;align-items:center;gap:12px}
.brand-mark{width:30px;height:30px;border-radius:50%;background:#b5b0aa}
.account-links{position:absolute;top:97px;right:156px;font-size:12px;color:#4b4037}
.account-links span{margin:0 6px}
.search{position:absolute;top:133px;left:821px;width:186px;height:37px;border:1px solid #cfcab7;background:#fff;display:flex}
.search .field{flex:1}
.search .btn{width:39px;border-left:1px solid #cfcab7;background:#f4f4f4;display:flex;align-items:center;justify-content:center}

.slider-band{position:absolute;top:206px;left:0;width:1200px;height:328px;background:linear-gradient(90deg,#8a3a1a,#b5582a 8%,#8a3a1a 15%,#8a3a1a 85%,#b5582a 92%,#8a3a1a)}
.slide{top:206px;height:328px;background:linear-gradient(90deg,#e6eef0 0%,#f1ecdf 35%,#eac9a4 55%,#e8bf95 75%,#d6e2e4 100%)}
.slide-title{position:absolute;left:53px;top:122px;font-family:"Magra",sans-serif;font-weight:700;font-size:29px;color:#b3100f}
.slide-sub{position:absolute;left:53px;top:160px;font-family:"Magra",sans-serif;font-size:27px;color:#b3100f}
.arrow{position:absolute;top:151px;width:30px;height:30px;border-radius:50%;background:#5b2020;display:flex;align-items:center;justify-content:center}
.arrow.prev{left:14px}.arrow.next{right:0}
.dots{position:absolute;left:395px;top:293px;display:flex;gap:9px}
.dots i{width:18px;height:18px;border-radius:50%;border:3px solid #2e2a22;background:#fff}
.dots i.on{background:var(--accent-red)}

.welcome-bar{top:546px;height:38px;background:var(--band-brown);color:#f3ede2;font-family:"Magra",sans-serif;font-size:19px;text-align:center;line-height:38px}
.zigzag{position:absolute;left:0;right:0;bottom:-6px;height:6px;background:linear-gradient(135deg,var(--band-brown) 50%,transparent 50%) 0 0/8px 6px,linear-gradient(225deg,var(--band-brown) 50%,transparent 50%) 0 0/8px 6px;background-repeat:repeat-x}

.features{top:613px;display:flex;justify-content:space-between}
.feature{width:205px;text-align:center}
.feature h2{font-family:"Magra",sans-serif;font-weight:400;font-size:18px;color:var(--title-red);height:37px}
.photo{width:178px;height:178px;border-radius:50%;border:4px solid #9a2a2a;margin:0 auto}
.feature p{font-size:11.4px;line-height:14px;margin:13px auto 0;width:195px;height:56px;color:#3f3630}
.know-more{display:inline-block;margin-top:8px;border:1px solid #d3cdb8;background:#fbf9ef;font-family:"Magra",sans-serif;font-size:14px;color:#8a8179;padding:5px 10px}

.newsletter{position:absolute;top:944px;left:0;width:1200px;height:59px;background:var(--news-band)}
.newsletter .container{top:10px;display:flex;align-items:center;gap:12px}
.newsletter h3{font-family:"Magra",sans-serif;font-weight:400;font-size:19px;color:#2f3a2f;width:240px;padding-left:39px}
.input{width:201px;height:37px;border:1px solid #d9d5c5;background:#f2f0e6;font-family:"Magra",sans-serif;font-size:18px;color:#c6c1b4;display:flex;align-items:center;justify-content:center}
.subscribe{width:131px;height:37px;background:var(--accent-red);color:#fff;font-family:"Magra",sans-serif;font-size:19px;display:flex;align-items:center;justify-content:center;border:1px solid #5a0707}

.footer{position:absolute;top:1003px;left:0;width:1200px;height:161px;background:var(--footer-dark)}
.footer .container{top:6px;display:flex;justify-content:space-between}
.footer-col{width:210px}
.footer-col h4{position:relative;background:var(--footer-head);color:#f3ece2;font-weight:400;font-size:14px;height:26px;line-height:26px;padding-left:16px}
.footer-col h4::after{content:"";position:absolute;left:0;right:0;bottom:-4px;height:4px;background:linear-gradient(135deg,var(--footer-head) 50%,transparent 50%) 0 0/6px 4px,linear-gradient(225deg,var(--footer-head) 50%,transparent 50%) 0 0/6px 4px;background-repeat:repeat-x}
.footer-col ul{list-style:none;margin-top:16px;font-size:11.6px;line-height:13.7px;color:var(--footer-text);padding-left:20px}
.footer-col li::before{content:"• "}
.footer-col li.wrap{padding-left:11px;text-indent:-11px}
.contact-line{display:flex;align-items:center;gap:14px;font-size:11.6px;color:var(--footer-text);margin:14px 0 0 20px}
.social{display:flex;gap:3px;margin:22px 0 0 23px}
.social i{width:20px;height:20px;background:#3a3532}

.copyright{position:absolute;top:1164px;left:0;width:1200px;height:36px;background:#1f1c1a;color:var(--footer-text);font-size:11.6px;text-align:center;line-height:36px}
</style>
</head>
<body>
<div class="top-strip"></div>
<div class="header-band"></div>

<nav class="container main-nav">
  <a class="active">Home</a><a>About Us</a><a>Our Services</a><a>Shadow Support</a><a>Clients</a><a>Contact Us</a>
</nav>

<div class="container brand"><span class="brand-mark"></span>Lantern Pathway</div>
<div class="account-links">Login<span>|</span>Register<span>|</span>Enquiry</div>
<div class="search"><div class="field"></div><div class="btn">
  <svg width="22" height="22" viewBox="0 0 22 22"><circle cx="8" cy="8" r="6" fill="none" stroke="#555" stroke-width="2.2"/><line x1="12.5" y1="12.5" x2="20" y2="19" stroke="#555" stroke-width="3"/></svg>
</div></div>

<div class="slider-band"></div>
<section class="container slide" role="img" aria-label="Photograph of a mother and daughter touching noses and smiling">
  <div class="slide-title">Suspendisse vulputate aliquam</div>
  <div class="slide-sub">Vivamus sollicitudin metus</div>
  <div class="arrow prev"><svg width="12" height="12" viewBox="0 0 12 12"><path d="M8 2 L4 6 L8 10" fill="none" stroke="#fff" stroke-width="2.4"/></svg></div>
  <div class="arrow next"><svg width="12" height="12" viewBox="0 0 12 12"><path d="M4 2 L8 6 L4 10" fill="none" stroke="#fff" stroke-width="2.4"/></svg></div>
  <div class="dots"><i class="on"></i><i></i><i></i><i></i></div>
</section>

<div class="container welcome-bar">Welcome to Lantern Pathway<div class="zigzag"></div></div>

<section class="container features">
  <div class="feature">
    <h2>About Shadow</h2>
    <div class="photo" role="img" aria-label="Photo of an open hand holding a seedling in soil" style="background:radial-gradient(circle at 50% 70%,#d9b9a0,#9fb7c2 60%,#7e9eae)"></div>
    <p>Lantern Pathway is part of the Kestrel Therapy Group of Companies, who are providing speech language therapy,</p>
    <span class="know-more">Know More</span>
  </div>
  <div class="feature">
    <h2>Vision &amp; Mission</h2>
    <div class="photo" role="img" aria-label="Photo of an elderly woman talking with a carer" style="background:linear-gradient(120deg,#b8b0a0,#e6e1d8 55%,#c9d2da)"></div>
    <p>Lantern Pathway was borne out of our Speech language Patholo-gists’ frustration at a frequent lack of carry-over of goals</p>
    <span class="know-more">Know More</span>
  </div>
  <div class="feature">
    <h2>Services</h2>
    <div class="photo" role="img" aria-label="Photo of a family of four sitting together" style="background:linear-gradient(160deg,#dfe5ea,#b7a89a 55%,#8fa6c0)"></div>
    <p>Provide families with well-trained Shadows who are mentored by Speech Language Pathologists and Professional Therapists.</p>
    <span class="know-more">Know More</span>
  </div>
  <div class="feature">
    <h2>Support</h2>
    <div class="photo" role="img" aria-label="Photo of a thoughtful woman in a group setting" style="background:linear-gradient(140deg,#9aa3ad,#e0d6c8 50%,#b7c3d1)"></div>
    <p>A shadow support is para-professional who can help a strugling student to integrate and learn in their school environment.</p>
    <span class="know-more">Know More</span>
  </div>
</section>

<section class="newsletter"><div class="container">
  <h3>Subscribe to Newsletter</h3>
  <div class="input">Enter Name</div>
  <div class="input">Email Address</div>
  <div class="subscribe">Subscribe</div>
</div></section>

<footer class="footer"><div class="container">
  <div class="footer-col"><h4>Main Menu</h4>
    <ul><li>Home</li><li>About Us</li><li>Services</li><li>Support</li><li>Clients</li><li>Contact Us</li></ul></div>
  <div class="footer-col"><h4>FAQ’s</h4>
    <ul style="padding-left:10px"><li>What is shadow support?</li><li>What are its Advantages?</li><li class="wrap">How do I know if my child needs shadowing ?</li></ul></div>
  <div class="footer-col"><h4>Testimonials</h4>
    <ul><li>Shadow Support will partic-ipate in a collaborative working relationship with the professio-nals working with each student to facilitate progress</li></ul></div>
  <div class="footer-col"><h4>Contact Us</h4>
    <div class="contact-line"><svg width="22" height="16" viewBox="0 0 22 16"><path d="M2 6 Q11 -1 20 6 L18 8 L15 6 L15 4 Q11 2 7 4 L7 6 L4 8 Z M5 9 H17 V15 H5 Z" fill="none" stroke="#8a8279" stroke-width="1.2"/></svg>+65 6100 2480</div>
    <div class="contact-line"><svg width="22" height="16" viewBox="0 0 22 16"><rect x="1" y="2" width="20" height="12" fill="none" stroke="#8a8279" stroke-width="1.2"/><path d="M1 2 L11 9 L21 2" fill="none" stroke="#8a8279" stroke-width="1.2"/></svg>hello@lanternpathway.com</div>
    <div class="social"><i></i><i></i><i></i><i></i></div>
  </div>
</div></footer>

<div class="copyright">Lantern Pathway © 2014 &nbsp;|&nbsp;&nbsp; Privacy Policy</div>
</body>
</html>
```